continued... Web Design for Professional Development and marketplace

in addition to the homepages that you are desiging, can you also create designs for the attached wireframes that are part of the same website.
I am creating this as a seperate project as we are keen to see your designs for the rest of the website.
VIdeo of prototype and homepage designs
https://www.quillvane.com/sh/rk7tpa2mw9qhb3c/8Lw2oNv4Zy/design
Updates
added an additional wireframe that was missed in the original upload
added one more wireframe for the homepage: where the user is prompted to login or signup
Industry/Entity Type
Marketplace
Look and feel
Each slider illustrates characteristics of the customer's brand and the style your logo design should communicate.

```html
<!DOCTYPE html>
<html lang="en">
<head>
<meta charset="utf-8">
<title>Add Review – Skillharbor</title>
<link href="https://fonts.googleapis.com/css2?family=Roboto:wght@400;500&display=swap" rel="stylesheet">
<style>
  :root {
    --page-bg: #f2f2f2;
    --panel-bg: #ffffff;
    --header-bg: #3b3b3b;
    --green: #2f9467;
    --green-light: #4bb587;
    --mint: #e4f4ec;
    --text: #444444;
    --line: #c9c9c9;
    --star-off: #7d8a93;
  }
  * { box-sizing: border-box; margin: 0; padding: 0; }
  html, body { width: 1200px; height: 1159px; overflow: hidden; }
  body { background: var(--page-bg); font-family: "Roboto", Arial, sans-serif; color: var(--text); position: relative; }
  .abs { position: absolute; }
  .panel { left: 246px; top: 26px; width: 700px; height: 1052px; background: var(--panel-bg); }

  .site-header { left: 246px; top: 26px; width: 700px; height: 51px; background: var(--header-bg); }
  .menu-btn { left: 10px; top: 9px; width: 34px; height: 34px; background: var(--green); display: flex; align-items: center; justify-content: center; }
  .search { left: 52px; top: 9px; width: 164px; height: 34px; background: #fff; font-size: 12px; color: #222; padding: 10px 14px; }
  .search svg { position: absolute; right: 7px; top: 6px; }
  .brand { left: 236px; top: 0; width: 156px; height: 51px; display: flex; align-items: center; justify-content: center; gap: 8px; color: #fff; font-size: 20px; font-weight: 400; white-space: nowrap; }
  .brand-mark { width: 12px; height: 12px; background: #fff; }
  .btn-add { left: 403px; top: 9px; width: 82px; height: 34px; background: #fff; color: #333; font-size: 11.5px; line-height: 1.1; display: flex; align-items: center; padding-left: 8px; gap: 7px; }
  .btn-login { left: 506px; top: 9px; width: 82px; height: 34px; background: var(--green); color: #fff; font-size: 12px; display: flex; align-items: center; padding-left: 8px; gap: 7px; }
  .btn-signup { left: 609px; top: 9px; width: 82px; height: 34px; background: #fff; color: #222; font-size: 12px; display: flex; align-items: center; justify-content: center; }

  .sub-nav { left: 246px; top: 77px; width: 700px; height: 25px; background: var(--mint); font-size: 10.5px; }
  .sub-nav span { position: absolute; top: 6px; }
  .sub-nav .strong { font-weight: 500; color: #555; }

  .filters { left: 246px; top: 102px; width: 700px; height: 52px; display: flex; }
  .filter { height: 52px; color: #fff; text-align: center; padding-top: 11px; font-size: 12px; line-height: 1; white-space: nowrap; }
  .filter.dark { background: var(--green); }
  .filter.light { background: var(--green-light); }
  .filter .caret { font-size: 8px; display: block; margin-top: 1px; }
  .filter .value { font-size: 8.5px; display: block; margin-top: 2px; }

  .crumbs { left: 260px; top: 167px; font-size: 10px; color: #555; }
  .crumbs a { color: #555; text-decoration: underline; }
  .page-title { left: 258px; top: 189px; font-size: 19px; font-weight: 500; color: var(--green); }
  .label { font-size: 10px; color: #555; }
  .stars { left: 260px; top: 248px; display: flex; gap: 4px; }
  .field { width: 242px; height: 34px; border: 1px solid var(--line); background: #fff; font-size: 10px; color: #555; padding: 11px 8px; }
  .chip { height: 34px; background: var(--green); color: #fff; font-size: 13px; display: flex; align-items: center; justify-content: center; letter-spacing: 0.3px; }
  .logo-slot { width: 90px; height: 90px; }
  .check { display: flex; align-items: center; font-size: 10px; color: #555; }
  .box { width: 9px; height: 9px; border: 1px solid #999; background: #f4f4f4; margin-right: 4px; }
  .textarea { left: 260px; top: 846px; width: 409px; height: 144px; border: 1px solid var(--line); }
  .submit { left: 585px; top: 1005px; width: 84px; height: 33px; background: var(--green); color: #fff; font-size: 13px; display: flex; align-items: center; justify-content: center; letter-spacing: 0.3px; }
</style>
</head>
<body>
  <div class="abs panel"></div>

  <header class="abs site-header">
    <div class="abs menu-btn">
      <svg width="24" height="18" viewBox="0 0 24 18"><g fill="#fff"><rect y="0" width="24" height="2.5"/><rect y="5" width="24" height="2.5"/><rect y="10" width="24" height="2.5"/><rect y="15" width="24" height="2.5"/></g></svg>
    </div>
    <div class="abs search">Search
      <svg width="22" height="22" viewBox="0 0 22 22"><circle cx="9" cy="9" r="7" fill="none" stroke="#111" stroke-width="2.4"/><line x1="14" y1="14" x2="20" y2="20" stroke="#111" stroke-width="2.8" stroke-linecap="round"/></svg>
    </div>
    <div class="abs brand"><span class="brand-mark"></span><span>Skillharbor</span></div>
    <div class="abs btn-add">
      <svg width="16" height="16" viewBox="0 0 16 16"><rect x="6" y="0" width="4" height="16" fill="#333"/><rect x="0" y="6" width="16" height="4" fill="#333"/></svg>
      <span>Add<br>Review</span>
    </div>
    <div class="abs btn-login">
      <svg width="14" height="16" viewBox="0 0 14 16"><circle cx="7" cy="4.5" r="4" fill="#fff"/><path d="M0 16c0-5 3-7 7-7s7 2 7 7z" fill="#fff"/></svg>
      <span>Login</span>
    </div>
    <div class="abs btn-signup">Sign up</div>
  </header>

  <nav class="abs sub-nav">
    <span class="strong" style="left:219px">About</span>
    <span class="strong" style="left:276px">Business</span>
    <span class="strong" style="left:348px">Developers</span>
    <span style="left:484px">Privacy &amp; Terms</span>
    <span style="left:583px">Copyright &amp; Trademark</span>
  </nav>

  <div class="abs filters">
    <div class="filter dark" style="width:72px">Save<span class="value" style="font-size:16px;margin-top:2px">+</span></div>
    <div class="filter light" style="width:76px">Career<span class="caret">▼</span><span class="value">(all)</span></div>
    <div class="filter dark" style="width:108px">Specialization<span class="caret">▼</span><span class="value">(all)</span></div>
    <div class="filter light" style="width:82px">Location<span class="caret">▼</span><span class="value">(Vancouver)</span></div>
    <div class="filter dark" style="width:60px">Price<span class="caret">▼</span><span class="value">($600-3000)</span></div>
    <div class="filter light" style="width:94px">Start Date<span class="caret">▼</span><span class="value">(2 - 6 months)</span></div>
    <div class="filter dark" style="width:62px">Level<span class="caret">▼</span><span class="value">(intermediate)</span></div>
    <div class="filter light" style="width:68px">Type<span class="caret">▼</span><span class="value">(multiple)</span></div>
    <div class="filter dark" style="width:78px">Provider<span class="caret">▼</span><span class="value">(one)</span></div>
  </div>

  <div class="abs crumbs"><a>Home</a> &nbsp;&gt;&nbsp; <a>Product Management</a></div>
  <h1 class="abs page-title">Add Review</h1>

  <div class="abs label" style="left:260px;top:227px">Rating</div>
  <div class="abs stars">
    <svg width="22" height="22" viewBox="0 0 24 24"><path d="M12 1l3.3 7.2 7.7.8-5.8 5.2 1.7 7.8L12 18l-6.9 4 1.7-7.8L1 9l7.7-.8z" fill="var(--green)"/></svg>
    <svg width="22" height="22" viewBox="0 0 24 24"><path d="M12 1l3.3 7.2 7.7.8-5.8 5.2 1.7 7.8L12 18l-6.9 4 1.7-7.8L1 9l7.7-.8z" fill="var(--green)"/></svg>
    <svg width="22" height="22" viewBox="0 0 24 24"><path d="M12 1l3.3 7.2 7.7.8-5.8 5.2 1.7 7.8L12 18l-6.9 4 1.7-7.8L1 9l7.7-.8z" fill="var(--green)"/></svg>
    <svg width="22" height="22" viewBox="0 0 24 24"><path d="M12 1l3.3 7.2 7.7.8-5.8 5.2 1.7 7.8L12 18l-6.9 4 1.7-7.8L1 9l7.7-.8z" fill="var(--green)"/></svg>
    <svg width="22" height="22" viewBox="0 0 24 24"><path d="M12 1l3.3 7.2 7.7.8-5.8 5.2 1.7 7.8L12 18l-6.9 4 1.7-7.8L1 9l7.7-.8z" fill="var(--star-off)"/></svg>
  </div>

  <div class="abs label" style="left:260px;top:290px">Provider</div>
  <div class="abs field" style="left:260px;top:310px">Provider URL</div>
  <div class="abs field" style="left:260px;top:350px">Provider Name</div>

  <div class="abs label" style="left:260px;top:404px">Category</div>
  <div class="abs field" style="left:260px;top:430px">Tags</div>
  <div class="abs chip" style="left:517px;top:430px;width:159px">Product Management</div>
  <div class="abs chip" style="left:690px;top:430px;width:84px">Marketing</div>

  <div class="abs label" style="left:260px;top:483px">Select Logo</div>
  <svg class="abs logo-slot" style="left:261px;top:506px" viewBox="0 0 90 90" role="img" aria-label="Provider logo option"><rect x="0.5" y="0.5" width="89" height="89" fill="none" stroke="var(--green)"/><path d="M0 0L90 90M90 0L0 90" stroke="var(--green)" stroke-width="0.8"/></svg>
  <svg class="abs logo-slot" style="left:365px;top:506px" viewBox="0 0 90 90" role="img" aria-label="Provider logo option"><rect x="0.5" y="0.5" width="89" height="89" fill="none" stroke="var(--green)"/><path d="M0 0L90 90M90 0L0 90" stroke="var(--green)" stroke-width="0.8"/></svg>
  <svg class="abs logo-slot" style="left:469px;top:506px" viewBox="0 0 90 90" role="img" aria-label="Provider logo option"><rect x="0.5" y="0.5" width="89" height="89" fill="none" stroke="var(--green)"/><path d="M0 0L90 90M90 0L0 90" stroke="var(--green)" stroke-width="0.8"/></svg>
  <svg class="abs logo-slot" style="left:573px;top:506px" viewBox="0 0 90 90" role="img" aria-label="Provider logo option"><rect x="0.5" y="0.5" width="89" height="89" fill="none" stroke="var(--green)"/><path d="M0 0L90 90M90 0L0 90" stroke="var(--green)" stroke-width="0.8"/></svg>

  <div class="abs label" style="left:260px;top:608px">Coures</div>
  <div class="abs field" style="left:260px;top:628px">Course name</div>
  <div class="abs field" style="left:260px;top:669px">Price</div>

  <svg class="abs" style="left:260px;top:718px" width="20" height="18" viewBox="0 0 20 18"><path d="M1 11L12 2l7 5-11 9z" fill="var(--green)"/><path d="M1 11l7 5v2l-7-5z" fill="var(--green)"/></svg>
  <div class="abs check" style="left:287px;top:721px"><span class="box"></span>&nbsp;Book</div>
  <svg class="abs" style="left:422px;top:718px" width="20" height="18" viewBox="0 0 20 18"><rect x="1" y="1" width="18" height="12" fill="none" stroke="var(--green)" stroke-width="2"/><rect x="8" y="13" width="4" height="3" fill="var(--green)"/><rect x="5" y="16" width="10" height="2" fill="var(--green)"/></svg>
  <div class="abs check" style="left:451px;top:721px"><span class="box"></span>&nbsp;Online</div>

  <svg class="abs" style="left:260px;top:768px" width="24" height="18" viewBox="0 0 24 18"><circle cx="6" cy="4" r="3" fill="var(--green)"/><circle cx="18" cy="4" r="3" fill="var(--green)"/><circle cx="12" cy="6" r="3.5" fill="var(--green)"/><path d="M0 14c0-4 3-6 6-6s6 2 6 6z" fill="var(--green)"/><path d="M12 14c0-4 3-6 6-6s6 2 6 6z" fill="var(--green)"/><path d="M5 18c0-5 3-7 7-7s7 2 7 7z" fill="var(--green)"/></svg>
  <div class="abs check" style="left:287px;top:771px"><span class="box"></span>&nbsp;Conference</div>
  <svg class="abs" style="left:427px;top:770px" width="14" height="17" viewBox="0 0 14 17"><circle cx="7" cy="4.5" r="4" fill="var(--green)"/><path d="M0 17c0-5 3-7.5 7-7.5s7 2.5 7 7.5z" fill="var(--green)"/></svg>
  <div class="abs check" style="left:451px;top:771px"><span class="box"></span>&nbsp;In Person Training</div>

  <div class="abs check" style="left:261px;top:822px"><span class="box"></span>&nbsp;Beginner</div>
  <div class="abs check" style="left:360px;top:822px"><span class="box"></span>&nbsp;Intermediate</div>
  <div class="abs check" style="left:483px;top:822px"><span class="box"></span>&nbsp;Advanced</div>

  <div class="abs textarea"></div>
  <div class="abs submit">Submit &gt;</div>
</body>
</html>
```